Business Card for Professional Photographer

I'm looking for an eye catching modern clean design that compliments my logo/ website fonts & colours.
I specialise in architecture, corporate & commercial photography so I'm marketing to professional clients rather than portrait / wedding clients.

I would prefer to not have a solid black design.

My logo brand guide is as follows :

Main front font. : Reislust
Main font colour : #fff
Slogan front font : Ubuntu Bold
Monogram front font : Venti Medium
Container colour : #fff

I need print ready files in pdf .png & .eps formats.

Included in the files below are some screen grabs as reference to font & colours etc.

```html
<!DOCTYPE html>
<html lang="en">
<head>
<meta charset="utf-8">
<title>Northlight Studio – Business Card</title>
<link rel="stylesheet" href="https://fonts.googleapis.com/css2?family=Montserrat:wght@300;400&family=Ubuntu:wght@400;700&family=Roboto:wght@400&display=swap">
<style>
  :root {
    --page-bg: #2a2a2b;
    --card-dark: #2b2b2e;
    --card-darker: #1c1c1f;
    --gold: #d4a94a;
    --gold-light: #f3dc93;
    --gold-deep: #c4953f;
    --ink: #111111;
    --white: #ffffff;
  }
  * { box-sizing: border-box; margin: 0; padding: 0; }
  html, body {
    width: 799px; height: 1200px; overflow: hidden;
    background: var(--page-bg);
  }
  .sheet {
    position: relative; width: 799px; height: 1200px;
    display: flex; flex-direction: column; align-items: center;
    justify-content: space-around; padding: 80px 0;
  }
  .card {
    position: relative; width: 680px; height: 389px;
    overflow: hidden; border-radius: 3px;
    box-shadow: 0 14px 30px rgba(0,0,0,.55);
  }

  /* Front */
  .card-front { background: var(--card-darker); }
  .front-photos {
    position: absolute; inset: 0;
    background:
      linear-gradient(135deg, rgba(60,62,70,.55) 0%, rgba(25,26,30,.2) 45%, rgba(70,64,55,.45) 100%),
      linear-gradient(90deg, #23262d 0%, #2c2a28 40%, #33312d 70%, #26272b 100%);
  }
  .front-brand {
    position: absolute; left: 150px; top: 150px;
  }
  .wordmark {
    font-family: "Montserrat", sans-serif; font-weight: 300;
    font-size: 33px; letter-spacing: 4px; color: var(--gold);
    text-transform: uppercase; white-space: nowrap;
  }
  .wordmark-row { display: flex; align-items: center; gap: 16px; }
  .brand-square {
    width: 58px; height: 58px; border: 3px solid var(--gold); border-radius: 6px;
  }
  .tagline {
    font-family: "Ubuntu", sans-serif; font-weight: 700;
    font-size: 11px; letter-spacing: 2.6px; color: var(--gold);
    margin-top: 4px; padding-left: 76px; white-space: nowrap;
  }
  .front-web {
    position: absolute; left: 224px; top: 268px;
    font-family: "Montserrat", sans-serif; font-weight: 400;
    font-size: 15px; letter-spacing: 3px; color: var(--gold);
  }

  /* Back */
  .card-back {
    background: linear-gradient(160deg, var(--gold-deep) 0%, var(--gold) 40%, var(--gold-light) 100%);
  }
  .back-split { position: absolute; inset: 0; }
  .holder {
    position: absolute; left: 30px; top: 28px;
    font-family: "Ubuntu", sans-serif;
  }
  .holder-name { font-weight: 700; font-size: 21px; color: var(--ink); letter-spacing: -.3px; }
  .holder-role { font-weight: 400; font-size: 13px; color: var(--ink); }
  .contacts {
    position: absolute; left: 30px; top: 190px;
    list-style: none; font-family: "Roboto", sans-serif;
    font-size: 15px; color: var(--ink); line-height: 22px;
  }
  .contacts li { display: flex; align-items: center; gap: 10px; }
  .contacts svg { width: 14px; height: 14px; flex: none; }
  .contacts .address { margin-top: 2px; }
  .back-brand {
    position: absolute; left: 360px; top: 140px; width: 300px;
    display: flex; flex-direction: column; align-items: center;
  }
  .back-brand .brand-square { width: 62px; height: 62px; margin-bottom: 16px; }
  .back-brand .wordmark { color: var(--white); font-size: 21px; letter-spacing: 3px; }
  .back-brand .tagline { padding-left: 0; font-size: 8.5px; letter-spacing: 2px; margin-top: 3px; }
</style>
</head>
<body>
<main class="sheet">

  <section class="card card-front" aria-label="Business card front">
    <div class="front-photos" role="img" aria-label="Darkened collage of architecture and commercial photographs"></div>
    <div class="front-brand">
      <div class="wordmark-row">
        <span class="brand-square"></span>
        <span class="wordmark">Northlight Studio</span>
      </div>
      <div class="tagline">Architecture Corporate Commercial</div>
    </div>
    <div class="front-web">www.northlightstudio.com.au</div>
  </section>

  <section class="card card-back" aria-label="Business card back">
    <svg class="back-split" viewBox="0 0 680 389" preserveAspectRatio="none" aria-hidden="true">
      <path d="M410 0 Q315 170 345 389 L680 389 L680 0 Z" fill="var(--card-dark)"/>
      <path d="M410 0 Q315 170 345 389" fill="none" stroke="var(--gold-light)" stroke-width="5" opacity=".8"/>
    </svg>

    <div class="holder">
      <div class="holder-name">Marcus Hale</div>
      <div class="holder-role">Photographer</div>
    </div>

    <ul class="contacts">
      <li>
        <svg viewBox="0 0 16 16"><path d="M3 1h3l1.5 4-2 1.3a9 9 0 0 0 4.2 4.2L11 8.5l4 1.5v3a2 2 0 0 1-2 2A12 12 0 0 1 1 3a2 2 0 0 1 2-2z" fill="var(--ink)"/></svg>
        0412555018
      </li>
      <li>
        <svg viewBox="0 0 16 16"><rect x="1" y="3" width="14" height="10" fill="var(--ink)"/><path d="M1 3l7 6 7-6" fill="none" stroke="var(--gold)" stroke-width="1.3"/></svg>
        info@northlightstudio.com.au
      </li>
      <li>
        <svg viewBox="0 0 16 16"><circle cx="8" cy="8" r="7" fill="var(--ink)"/><path d="M1 8h14M8 1c-3 4-3 10 0 14M8 1c3 4 3 10 0 14" fill="none" stroke="var(--gold)" stroke-width="1"/></svg>
        www.northlightstudio.com.au
      </li>
      <li class="address">48 Mill Lane Ashford Vic 3190</li>
    </ul>

    <div class="back-brand">
      <span class="brand-square"></span>
      <div class="wordmark">Northlight Studio</div>
      <div class="tagline">Architecture Corporate Commercial</div>
    </div>
  </section>

</main>
</body>
</html>
```